New Business Card Design Project

I need a design for business cards, i am an electrical business called "Corvane Electrical and Communications" i need the cards to be double sided with the company logo on the back (attached) the front needs to say my company name, web site, email address, telephone number, and ABN number and electrical license number. I am open to different arrangements of the information but would like the background to be incorporating something electrical or something that looks smart. open to all additional ideas also.

The company colours are orange and grey see logo attached.

Business Name: Corvane Electrical and Communications
Website: corvaneelectricalandcomms.example.com.au
Email: brent@corvaneelectricalandcomms.example.com.au
Telephone(mobile): 0481209736
ABN: 71208349162
Lic No: 418273D

Target Market(s)

Business entities, Project Managers, Accounts, Clients

Industry/Entity Type

Electrician

Contact Information for Business Card

I need a design for business cards, i am an electrical business called "Corvane Electrical and Communications" i need the cards to be double sided with the company logo on the back (attached) the front needs to say my company name

Font styles to use
Serif
Sans Serif

Colors
f37122
5c5c5c

Requirements
Must have
• Must have the Logo on the back open to different ways of it being on the back but had in mind to keep it central but again open to other options
Nice to have
• A real modern cool background that is eye catching yet contemporary
Should not have
• No backgrounds of a light bulb or plug or anything like that

```html
<!DOCTYPE html>
<html lang="en">
<head>
<meta charset="utf-8">
<title>Corvane Electrical and Communications – Business Cards</title>
<link rel="stylesheet" href="https://fonts.googleapis.com/css2?family=Arimo:wght@400;700&display=swap">
<style>
  :root {
    --orange: #f37122;
    --orange-soft: #f6a33a;
    --grey: #5c5c5c;
    --grey-dark: #3e3e3e;
    --grey-deep: #2f2f2f;
    --silver: #e4e4e4;
    --white: #ffffff;
    --stage: #ececec;
  }
  * { box-sizing: border-box; margin: 0; padding: 0; }
  html, body { width: 1200px; height: 950px; overflow: hidden; }
  body {
    background: var(--stage);
    font-family: "Arimo", Arial, sans-serif;
    display: flex;
    flex-direction: column;
    align-items: center;
    justify-content: center;
    gap: 50px;
  }
  .card {
    position: relative;
    width: 700px;
    height: 400px;
    border-radius: 6px;
    overflow: hidden;
    box-shadow: 0 8px 24px rgba(0,0,0,0.18);
  }

  /* Shared brand lockup */
  .brand {
    display: flex;
    align-items: center;
    gap: 16px;
    color: var(--silver);
    font-weight: 400;
  }
  .brand__dot {
    width: 18px; height: 18px;
    border-radius: 50%;
    background: var(--orange);
    flex: none;
  }
  .brand__text { display: flex; flex-direction: column; line-height: 1; }
  .brand__name { font-size: 64px; letter-spacing: 6px; }
  .brand__tagline { font-size: 15px; letter-spacing: 2.4px; margin-top: 8px; }

  /* Back side */
  .card--back {
    background: linear-gradient(120deg, var(--grey) 0%, var(--grey-dark) 55%, var(--grey-deep) 100%);
    display: flex;
    flex-direction: column;
    align-items: center;
    justify-content: center;
  }
  .card--back .brand__name { font-size: 76px; }
  .card--back .brand__tagline { font-size: 17px; }
  .back-web {
    margin-top: 26px;
    color: #9a9a9a;
    font-size: 16px;
    letter-spacing: 0.5px;
  }

  /* Front side */
  .card--front { background: var(--white); }
  .front-band {
    position: absolute;
    left: 0; right: 0;
    top: 108px; height: 184px;
    background: linear-gradient(90deg, var(--grey-dark) 0%, var(--grey) 50%, var(--grey-dark) 100%);
    border-top: 4px solid var(--orange);
    border-bottom: 4px solid var(--orange-soft);
    display: flex;
    flex-direction: column;
    align-items: center;
    justify-content: center;
  }
  .front-band .brand__name { font-size: 50px; letter-spacing: 5px; }
  .front-band .brand__tagline { font-size: 12px; letter-spacing: 2px; margin-top: 6px; }
  .registration {
    margin-top: 16px;
    color: var(--white);
    font-size: 14px;
    letter-spacing: 0.5px;
  }
  .holder {
    position: absolute;
    left: 40px; top: 30px;
    line-height: 1.15;
  }
  .holder__name { color: var(--orange); font-size: 22px; letter-spacing: 1px; }
  .holder__role { color: var(--grey); font-size: 15px; letter-spacing: 1px; }
  .contacts {
    position: absolute;
    right: 30px; bottom: 20px;
    list-style: none;
    color: var(--grey);
    font-size: 13.5px;
    line-height: 1.6;
  }
  .contacts li { display: flex; align-items: center; gap: 8px; }
  .contacts svg { width: 12px; height: 12px; flex: none; }
</style>
</head>
<body>

  <section class="card card--back" aria-label="Card back">
    <div class="brand">
      <span class="brand__dot"></span>
      <span class="brand__text">
        <span class="brand__name">CORVANE</span>
        <span class="brand__tagline">ELECTRICAL &amp; COMMUNICATIONS</span>
      </span>
    </div>
    <p class="back-web">corvaneelectricalandcomms.example.com.au</p>
  </section>

  <section class="card card--front" aria-label="Card front">
    <div class="holder">
      <p class="holder__name">MARLO TENNANT</p>
      <p class="holder__role">PRESIDENT</p>
    </div>

    <div class="front-band">
      <div class="brand">
        <span class="brand__dot"></span>
        <span class="brand__text">
          <span class="brand__name">CORVANE</span>
          <span class="brand__tagline">ELECTRICAL &amp; COMMUNICATIONS</span>
        </span>
      </div>
      <p class="registration">ABN: 71208349162 | Lic No: 418273D</p>
    </div>

    <ul class="contacts">
      <li>
        <svg viewBox="0 0 12 12" aria-hidden="true"><rect x="3" y="0.5" width="6" height="11" rx="1.2" fill="none" stroke="#f37122" stroke-width="1.4"/></svg>
        0481209736
      </li>
      <li>
        <svg viewBox="0 0 12 12" aria-hidden="true"><rect x="0.5" y="2" width="11" height="8" fill="#f37122"/><path d="M0.5,2 L6,7 L11.5,2" fill="none" stroke="#fff" stroke-width="1"/></svg>
        brent@corvaneelectricalandcomms.example.com.au
      </li>
      <li>
        <svg viewBox="0 0 12 12" aria-hidden="true"><circle cx="6" cy="6" r="5.5" fill="#f37122"/><path d="M0.5,6 H11.5 M6,0.5 C3,4 3,8 6,11.5 M6,0.5 C9,4 9,8 6,11.5" fill="none" stroke="#fff" stroke-width="0.8"/></svg>
        corvaneelectricalandcomms.example.com.au
      </li>
    </ul>
  </section>

</body>
</html>
```